Flat bootstrap design for existing site

I'm looking for a modern flat design based around an existing logo. This has to be a custom design (no external templates), and implemented into a bootstrap framework.

The logo is attached as 2 versions - choose whichever you want, that flows better with whatever design you choose.

Added screenshots of the existing site (currently using the default bootstrap layouts). Please make your designs around those pages in the screenshots (i.e. the homepage only has the postal code input and the header). The active page has 3 screenshots, because I wanted to illustrate the other states that would be visible (in the table rows).

This is a moving/junk removal website, just for some context.

Here's some example websites (flat designs) that I like, just to give you an idea of what I'm after.

https://www.plimvora.com/
https://dacklow.com/
https://trevanu.com/
https://quobrintal.com/en/

Coding

Coded - Design and coding required

Number of Pages Required

5+ page

Colors

Designer to choose colors to be used in the design.

Requirements
Must have
• It must be a modern/simple flat design, that is built around the existing logo (attached).
• It has to be implemented using bootstrap.

```html
<!DOCTYPE html>
<html lang="en">
<head>
<meta charset="utf-8">
<title>HAULVEX – Booking details</title>
<link rel="stylesheet" href="https://fonts.googleapis.com/css2?family=Montserrat:wght@600;700&family=Roboto:wght@400;500&family=Mulish:wght@400;600;700&display=swap">
<style>
  :root{
    --sky:#38bdf2;
    --sky-deep:#0f83c9;
    --purple:#5a4fcf;
    --purple-title:#5b4ca8;
    --ink:#2e2e3a;
    --text:#4a4a55;
    --line:#e2e4ea;
    --alert-bg:#d6eef8;
    --alert-line:#9fd8ef;
    --green:#8cc63f;
    --light-blue:#7fd1f2;
    --grey:#d6d8dc;
    --white:#ffffff;
    --footer-ink:#4a4a5c;
    --icon-grey:#8f96a3;
  }
  *{box-sizing:border-box;margin:0;padding:0}
  html,body{width:1200px;height:774px;overflow:hidden}
  body{position:relative;background:var(--sky);font-family:"Mulish",sans-serif;color:var(--text)}

  .site-header{position:absolute;left:144px;top:0;width:912px;height:80px}
  .brand{position:absolute;left:0;top:22px;display:flex;align-items:center;gap:8px;font-family:"Montserrat",sans-serif;font-weight:700;font-size:30px;color:var(--white);letter-spacing:1px}
  .brand-dot{width:16px;height:16px;border-radius:50%;background:var(--white)}
  .nav{position:absolute;right:0;top:22px;display:flex;align-items:center;height:35px;font-family:"Montserrat",sans-serif;font-weight:700;font-size:11.5px;letter-spacing:.6px;color:var(--white)}
  .nav a{color:inherit;text-decoration:none}
  .nav .link{margin-right:26px}
  .nav .driver-btn{background:var(--sky-deep);height:35px;line-height:35px;padding:0 11px;border-radius:2px;margin-right:16px;margin-left:6px}
  .user{display:flex;align-items:center;gap:6px;color:var(--purple);font-weight:600;font-size:12.5px;letter-spacing:.3px}
  .user-icon{width:18px;height:18px;border-radius:50%;background:var(--purple);display:flex;align-items:center;justify-content:center}

  .card{position:absolute;left:144px;width:912px;background:var(--white);border-radius:3px;box-shadow:0 4px 14px rgba(0,60,110,.12)}
  .card-title{font-family:"Roboto",sans-serif;font-weight:400;font-size:20px;color:var(--purple-title);padding:0 15px;height:47px;line-height:50px;border-bottom:1px solid var(--line)}
  .booking{top:102px;height:154px}
  .collapse-btn{position:absolute;right:16px;top:9px;width:29px;height:29px;border-radius:50%;border:1.5px solid #c9c6ea;display:flex;align-items:center;justify-content:center}
  .field-label{position:absolute;top:67px;font-size:13px;color:var(--ink);font-weight:600}
  .field{position:absolute;top:86px;height:36px;border:1px solid var(--line);border-radius:2px;font-size:12.5px;color:var(--ink);padding-left:11px;line-height:34px}
  .field.select{border-color:var(--purple)}
  .field .suffix{position:absolute;right:0;top:0;width:31px;height:34px;border-left:1px solid var(--line);display:flex;align-items:center;justify-content:center}
  .update-btn{position:absolute;left:823px;top:86px;width:73px;height:36px;background:var(--purple);color:var(--white);border-radius:2px;font-family:"Montserrat",sans-serif;font-weight:700;font-size:11px;letter-spacing:.8px;text-align:center;line-height:36px}

  .drivers{top:272px;height:336px}
  .notice{position:absolute;left:16px;top:64px;width:880px;height:36px;background:var(--alert-bg);border:1px solid var(--alert-line);border-radius:3px;font-size:12.5px;color:var(--text);padding-left:19px;line-height:34px}
  .driver-table{position:absolute;left:16px;top:122px;width:880px;border-collapse:collapse;font-size:12.5px;color:var(--ink)}
  .driver-table th{text-align:left;font-weight:700;font-size:12.5px;height:32px;vertical-align:top;padding-top:5px;border-bottom:1px solid var(--line)}
  .driver-table td{height:41.6px;border-bottom:1px solid var(--line);vertical-align:middle}
  .driver-table tr:last-child td{border-bottom:none}
  .col-name{width:179px}
  .col-dist{width:194px}
  .col-time{width:195px}
  .col-status{width:178px}
  .driver-table td.time{text-align:center;padding-right:60px}
  .badge{display:inline-block;width:92px;height:18px;line-height:18px;text-align:center;font-size:11px;color:var(--white)}
  .badge.accepted{background:var(--green)}
  .badge.sent{background:var(--light-blue)}
  .badge.pending{background:var(--grey)}
  .pay-btn{display:inline-block;background:var(--purple);color:var(--white);font-size:11.5px;width:105px;height:24px;line-height:24px;text-align:center;border-radius:2px;margin-left:10px}

  .scene-art{position:absolute;left:1010px;top:545px;width:190px;height:164px;border-radius:110px 0 0 0;background:linear-gradient(160deg,#8ed8f5,#6cc5ee)}

  .site-footer{position:absolute;left:0;top:709px;width:1200px;height:58px;background:var(--white)}
  .copyright{position:absolute;left:144px;top:23px;font-size:12.5px;color:var(--footer-ink)}
  .social{position:absolute;right:144px;top:20px;display:flex;gap:6px}
  .social span{width:19px;height:19px;background:var(--icon-grey);border-radius:2px}
  .footer-bar{position:absolute;left:0;top:767px;width:1200px;height:7px;background:var(--purple)}
</style>
</head>
<body>
  <header class="site-header">
    <div class="brand"><span class="brand-dot"></span>HAULVEX</div>
    <nav class="nav">
      <a class="link" href="#">BOOK</a>
      <a class="link" href="#">HOW IT WORKS</a>
      <a class="driver-btn" href="#">BECOME A DRIVER</a>
      <div class="user">
        <span class="user-icon"><svg width="10" height="10" viewBox="0 0 10 10"><circle cx="5" cy="3.3" r="2" fill="none" stroke="#fff" stroke-width="1.2"/><path d="M1.5 9.5c0-2 1.6-3 3.5-3s3.5 1 3.5 3" fill="none" stroke="#fff" stroke-width="1.2"/></svg></span>
        rowan@mailbox.test
        <svg width="10" height="7" viewBox="0 0 10 7"><path d="M1 1l4 4 4-4" fill="none" stroke="#5a4fcf" stroke-width="1.6"/></svg>
      </div>
    </nav>
  </header>

  <section class="card booking">
    <h2 class="card-title">Booking details</h2>
    <div class="collapse-btn"><svg width="11" height="7" viewBox="0 0 11 7"><path d="M1 6l4.5-4.5L10 6" fill="none" stroke="#5a4fcf" stroke-width="1.6"/></svg></div>
    <label class="field-label" style="left:16px">Package selected:</label>
    <div class="field select" style="left:16px;width:202px">Package 1
      <svg style="position:absolute;right:8px;top:9px" width="10" height="17" viewBox="0 0 10 17"><path d="M1.5 5l3.5-3.5L8.5 5M1.5 12l3.5 3.5 3.5-3.5" fill="none" stroke="#5a4fcf" stroke-width="1.4"/></svg>
    </div>
    <label class="field-label" style="left:230px">Pick-up time selected:</label>
    <div class="field" style="left:230px;width:222px">July 18 at 4:13 am
      <span class="suffix"><svg width="14" height="14" viewBox="0 0 14 14"><rect x="1" y="2.5" width="12" height="10.5" rx="1" fill="none" stroke="#5a4fcf" stroke-width="1.4"/><path d="M1 6h12M4 1v3M10 1v3" stroke="#5a4fcf" stroke-width="1.4"/></svg></span>
    </div>
    <label class="field-label" style="left:464px">Description:</label>
    <div class="field" style="left:464px;width:347px">1 Large Stove</div>
    <div class="update-btn">UPDATE</div>
  </section>

  <section class="card drivers">
    <h2 class="card-title">Drivers in your area</h2>
    <div class="notice">Please stay on this page and be patient, while we contact the drivers and find you one ASAP.</div>
    <table class="driver-table">
      <thead>
        <tr><th class="col-name">Name</th><th class="col-dist">Distance (KM)</th><th class="col-time">Agreed pick-up time</th><th class="col-status"></th><th></th></tr>
      </thead>
      <tbody>
        <tr><td>Garth Bellamy</td><td>4.04 KM away</td><td class="time">July 18 at 4:13 am</td><td><span class="badge accepted">Time accepted</span></td><td><span class="pay-btn">Make Payment</span></td></tr>
        <tr><td>Owen Prescott</td><td>5.07 KM away</td><td class="time">-</td><td><span class="badge sent">Request sent</span></td><td></td></tr>
        <tr><td>Milo Fenwick</td><td>11.13 KM away</td><td class="time">-</td><td><span class="badge sent">Request sent</span></td><td></td></tr>
        <tr><td>Dale Marlowe</td><td>11.91 KM away</td><td class="time">-</td><td><span class="badge pending">Pending</span></td><td></td></tr>
      </tbody>
    </table>
  </section>

  <div class="scene-art" role="img" aria-label="Illustration of a mover with bins beside a house and a branded moving van on a hill"></div>

  <footer class="site-footer">
    <p class="copyright">© 2017 HAULVEX. All rights reserved.</p>
    <div class="social"><span></span><span></span><span></span></div>
  </footer>
  <div class="footer-bar"></div>
</body>
</html>
```